Business card - mobile service

O KiraLink is a mobile family safety service based on tablets and smartphones.
The business card must have:
BASIC INFO
Company Logo
Name
Position / Job Title: Co-founder
Mobile Phone Number: +55 (11) 5080 6192
Land Line: +55 (11) 8765 093412
Email Address: name@kiralink-example.com
Web Site URL: www.kiralink-example.com
PROMOTIONAL INFO
Try KiraLink free Today!
Your personal promo code: qqqq-5151-hhhh-3030-9876
Promo code text explanation with the instructions about the trial offer
Updates
Dears,
One more must have: the KiraLink slogan:
Industry/Entity Type
Safety
Look and feel
Each slider illustrates characteristics of the customer's brand and the style your logo design should communicate.

```html
<!DOCTYPE html>
<html lang="en">
<head>
<meta charset="utf-8">
<title>KiraLink business card</title>
<link rel="stylesheet" href="https://fonts.googleapis.com/css2?family=Poppins:wght@500;600;700&display=swap">
<style>
  :root {
    --stage: #3b3b3d;
    --sky: #12b4ec;
    --sky-light: #3fc6f3;
    --sky-deep: #0aa3dc;
    --sun: #ffcc0a;
    --white: #ffffff;
    --paper: #f6f8f9;
    --paper-tint: #e9f3f7;
    --ink-blue: #1aa7e3;
  }
  * { box-sizing: border-box; margin: 0; padding: 0; }
  html, body { width: 1200px; height: 874px; overflow: hidden; }
  body {
    background: var(--stage);
    font-family: "Poppins", sans-serif;
    display: flex;
    align-items: center;
    justify-content: center;
    gap: 29px;
  }
  .card {
    position: relative;
    width: 533px;
    height: 303px;
    border-radius: 16px;
    overflow: hidden;
    box-shadow: 0 6px 18px rgba(0,0,0,.45);
  }
  .card__band {
    position: absolute;
    left: 0; right: 0; bottom: 0;
    height: 33px;
    background: var(--sun);
    color: var(--white);
    font-weight: 500;
    font-size: 22px;
    line-height: 33px;
    text-align: center;
    letter-spacing: .5px;
  }
  .wordmark { font-weight: 700; line-height: 1; letter-spacing: -1px; }
  .slogan { font-weight: 600; font-size: 25px; line-height: 1; }
  .slogan .accent { color: var(--sun); }

  /* front */
  .card--front {
    background: linear-gradient(125deg, var(--sky-light) 0%, var(--sky) 45%, var(--sky-deep) 100%);
    color: var(--white);
  }
  .card--front .wordmark {
    position: absolute; top: 64px; left: 0; right: 0;
    text-align: center; font-size: 60px; color: var(--white);
  }
  .card--front .slogan {
    position: absolute; top: 127px; left: 0; right: 0;
    text-align: center; color: var(--white);
  }
  .holder {
    position: absolute; top: 213px; left: 0; right: 0;
    text-align: center; font-weight: 600; font-size: 18px;
  }
  .holder .divider { margin: 0 6px; }
  .contacts {
    position: absolute; top: 244px; left: 0; right: 0;
    display: flex; justify-content: center; gap: 20px;
    font-weight: 600; font-size: 12px;
  }
  .contact { display: flex; align-items: center; gap: 4px; }
  .contact__icon { width: 14px; height: 14px; flex: none; }
  .contact--email { text-transform: uppercase; }

  /* back */
  .card--back { background: var(--paper); }
  .card--back .texture {
    position: absolute; inset: 0 0 33px 0;
    background: linear-gradient(115deg, var(--paper) 0%, var(--paper-tint) 50%, var(--paper) 100%);
  }
  .card--back .wordmark {
    position: absolute; top: 38px; left: 0; right: 0;
    text-align: center; font-size: 58px; color: var(--ink-blue);
  }
  .card--back .slogan {
    position: absolute; top: 134px; left: 0; right: 0;
    text-align: center; font-size: 18px; color: var(--ink-blue);
  }
  .promo {
    position: absolute; top: 198px; left: 0; right: 0;
    text-align: center; color: var(--ink-blue); font-weight: 600;
  }
  .promo__title { font-size: 17px; line-height: 1.2; }
  .promo__title .free { color: var(--sun); text-transform: uppercase; }
  .promo__code, .promo__note { font-size: 11.5px; line-height: 1.3; }
  .promo__code span { text-transform: uppercase; }
</style>
</head>
<body>
  <section class="card card--front">
    <div class="wordmark">KiraLink</div>
    <p class="slogan"><span class="accent">Your</span> Family Safety <span class="accent">Service</span></p>
    <p class="holder">Marina Coelho<span class="divider">|</span>Co-founder</p>
    <div class="contacts">
      <span class="contact">
        <svg class="contact__icon" viewBox="0 0 14 14" aria-hidden="true"><rect width="14" height="14" rx="3" fill="#ffcc0a"/><rect x="4.5" y="2.5" width="5" height="9" rx="1" fill="none" stroke="#fff" stroke-width="1.3"/></svg>
        +55 (11) 5080 6192
      </span>
      <span class="contact">
        <svg class="contact__icon" viewBox="0 0 14 14" aria-hidden="true"><rect width="14" height="14" rx="3" fill="#ffcc0a"/><path d="M4 3.2c.6-.4 1.2-.3 1.5.3l.7 1.4c.2.4 0 .8-.3 1l-.5.4c.5 1 1.3 1.8 2.3 2.3l.4-.5c.3-.3.7-.4 1-.2l1.4.7c.6.3.7.9.3 1.5-.6.8-1.6 1-2.6.5C5.9 9.6 4.4 8.1 3.6 6c-.4-1-.2-2.1.4-2.8z" fill="#fff"/></svg>
        +55 (11) 8765 093412
      </span>
      <span class="contact contact--email">
        <svg class="contact__icon" viewBox="0 0 14 14" aria-hidden="true"><rect width="14" height="14" rx="3" fill="#ffcc0a"/><rect x="2.8" y="4" width="8.4" height="6" fill="none" stroke="#fff" stroke-width="1.2"/><path d="M2.8 4l4.2 3.3L11.2 4" fill="none" stroke="#fff" stroke-width="1.2"/></svg>
        name@kiralink-example.com
      </span>
    </div>
    <div class="card__band">www.kiralink-example.com</div>
  </section>

  <section class="card card--back">
    <div class="texture" role="img" aria-label="Faint repeating brand-name texture across the card background"></div>
    <div class="wordmark">KiraLink</div>
    <p class="slogan"><span class="accent">Your</span> Family Safety <span class="accent">Service</span></p>
    <div class="promo">
      <p class="promo__title">Try KiraLink <span class="free">free</span> Today!</p>
      <p class="promo__code">Your personal promo code: <span>qqqq-5151-hhhh-3030-9876</span></p>
      <p class="promo__note">Promo code text explanation with the instruction about the trial offer.</p>
    </div>
    <div class="card__band">www.kiralink-example.com</div>
  </section>
</body>
</html>
```